Business cards for Harbourline Supply Pty Ltd that import building products into Australia from China
Target Market(s)
Business to Business
Industry/Entity Type
Business
Contact Information for Business Card
Front: Logo and Business Name
Rear:
Desmond Varrick
General Manager
Mobile: 0427 561 394
email: dessie@harbourlinesupply.com.au
alternative email: dessie@outbackworks.com.au
web: www.harbourlinesupply.com.au
Adelaide, Brisbane and Darwin
Colors
ec1f27
fbee3d

```html
<!DOCTYPE html>
<html lang="en">
<head>
<meta charset="utf-8">
<title>Harbourline Supply Pty Ltd – Business Cards</title>
<link rel="stylesheet" href="https://fonts.googleapis.com/css2?family=Saira:wght@400;500;600;700&display=swap">
<style>
  :root {
    --backdrop: #bfbdbe;
    --card-white: #fdfdfd;
    --card-dark: #232323;
    --brand-red: #ec1f27;
    --brand-yellow: #fbee3d;
    --ink: #1c1c1c;
    --ink-soft: #2b2b2b;
    --white: #ffffff;
  }
  * { margin: 0; padding: 0; box-sizing: border-box; }
  html, body {
    width: 1200px; height: 900px; overflow: hidden;
    background: var(--backdrop);
    font-family: "Saira", "Arial", sans-serif;
  }
  .canvas { position: relative; width: 1200px; height: 900px; }

  .card {
    position: absolute; top: 271px;
    width: 458px; height: 281px;
    border-radius: 14px; overflow: hidden;
    box-shadow: 0 3px 5px rgba(0,0,0,0.35);
  }
  .card--contact { left: 137px; background: var(--card-white); }
  .card--brand { left: 626px; background: var(--card-dark); }

  .card__band {
    position: absolute; top: 0; right: 0;
    width: 99px; height: 100%;
    background: var(--card-dark);
  }

  .wordmark {
    position: absolute; left: 28px; top: 24px;
    font-weight: 700; font-size: 25px; line-height: 1.05;
    color: var(--ink); letter-spacing: -0.3px;
  }

  .person { position: absolute; left: 27px; top: 105px; }
  .person__name {
    font-weight: 700; font-size: 19px; letter-spacing: 0.4px;
    color: var(--ink); line-height: 1;
  }
  .person__name .first { color: var(--brand-red); }
  .person__role {
    margin-top: 4px; font-size: 13px; font-weight: 500; color: var(--ink-soft);
  }

  .contacts { position: absolute; left: 27px; top: 158px; list-style: none; }
  .contacts li {
    display: flex; align-items: center; gap: 9px;
    height: 19px; font-size: 13px; color: var(--ink-soft);
  }
  .contacts svg { width: 11px; height: 11px; fill: var(--brand-red); flex: none; }

  .locations {
    position: absolute; left: 28px; top: 240px;
    font-size: 13px; color: var(--ink-soft);
  }

  .brand-lockup {
    position: absolute; left: 0; right: 0; top: 110px;
    display: flex; align-items: center; justify-content: center; gap: 12px;
  }
  .brand-lockup__square {
    width: 26px; height: 26px; background: var(--brand-red);
  }
  .brand-lockup__name {
    font-weight: 700; font-size: 26px; color: var(--white); letter-spacing: -0.3px;
  }
</style>
</head>
<body>
<main class="canvas">
  <section class="card card--contact" aria-label="Contact side">
    <div class="wordmark">Harbourline Supply<br>Pty Ltd</div>

    <div class="person">
      <p class="person__name"><span class="first">DESMOND</span> VARRICK</p>
      <p class="person__role">General Manager</p>
    </div>

    <ul class="contacts">
      <li>
        <svg viewBox="0 0 12 12" aria-hidden="true"><path d="M1 4.5C1 2.5 3 1.5 6 1.5s5 1 5 3l-2.2.6-.3-1.4h-5l-.3 1.4zM3 6h6l1.5 4.5h-9z"/></svg>
        0427 561 394
      </li>
      <li>
        <svg viewBox="0 0 12 12" aria-hidden="true"><path d="M1 2.5h10v7H1zM1.8 3.3 6 6.6l4.2-3.3z" fill-rule="evenodd"/></svg>
        dessie@harbourlinesupply.com.au
      </li>
      <li>
        <svg viewBox="0 0 12 12" aria-hidden="true"><path d="M1 2.5h10v7H1zM1.8 3.3 6 6.6l4.2-3.3z" fill-rule="evenodd"/></svg>
        dessie@outbackworks.com.au
      </li>
      <li>
        <svg viewBox="0 0 12 12" aria-hidden="true"><circle cx="6" cy="6" r="5"/><path d="M3.5 4.5 5 3.5l1 1.5-1 1.5 1.5 2-2 .5zM7.5 3l1.5 1-1 1z" fill="#fff"/></svg>
        www.harbourlinesupply.com.au
      </li>
    </ul>

    <p class="locations">Adelaide, Brisbane and Darwin</p>

    <div class="card__band"></div>
  </section>

  <section class="card card--brand" aria-label="Brand side">
    <div class="brand-lockup">
      <span class="brand-lockup__square"></span>
      <span class="brand-lockup__name">Harbourline Supply Pty Ltd</span>
    </div>
  </section>
</main>
</body>
</html>
```